Tandem Hearth Works Pty Ltd

We need business cards for a company based in Perth, we install, service and maintain fire equipment.
On the front we want a great design with our logo and a small spot for our full company name, general company email address and office number. On the back we need space for our name, title, mobile number and email address on the back.

Target Market(s)

Facility managers and commercial/industrial building owners/occupiers.

Contact Information for Business Card

Font styles to use
Sans Serif

Requirements
Must have
• Please only submit 5 of your best samples.
Darker tones are preferred.
Nice to have
• We want to use, black, red and grey. Keep it modern and clean.
I've attached the company logo and a sample of a boarder we use on our emergency plans.
Should not have
• No preference. Let the designer choose.

```html
<!DOCTYPE html>
<html lang="en">
<head>
<meta charset="utf-8">
<title>Tandem Hearth Works Pty Ltd — Business Cards</title>
<link rel="stylesheet" href="https://fonts.googleapis.com/css2?family=Arimo:wght@400;700&display=swap">
<style>
  :root {
    --backdrop: #2b2b2d;
    --card: #1c1d1f;
    --card-edge: #232427;
    --pattern-top: #26272a;
    --pattern-bottom: #1c1d1f;
    --red: #ec1c24;
    --grey-light: #d9d9d9;
    --grey-mid: #bfbfbf;
    --rule: #55575b;
  }
  * { box-sizing: border-box; margin: 0; padding: 0; }
  html, body {
    width: 1200px; height: 1108px; overflow: hidden;
    background: var(--backdrop);
    font-family: "Arimo", Arial, sans-serif;
  }
  .canvas {
    position: relative; width: 1200px; height: 1108px;
    display: flex; justify-content: center; align-items: center; gap: 80px;
  }
  .card {
    position: relative; width: 440px; height: 700px;
    background: var(--card); border-radius: 22px; overflow: hidden;
    box-shadow: 0 14px 30px rgba(0,0,0,.45);
  }

  /* Front: person card */
  .brand-mark {
    position: absolute; left: 0; right: 0; top: 150px;
    display: flex; justify-content: center; align-items: flex-start; gap: 16px;
  }
  .brand-square { width: 26px; height: 26px; background: var(--red); margin-top: 6px; }
  .brand-name {
    color: var(--red); font-weight: 700; font-size: 40px; line-height: 1.05;
    text-transform: uppercase; letter-spacing: .5px;
  }
  .person {
    position: absolute; left: 0; right: 0; top: 450px; text-align: center;
  }
  .person-name {
    color: var(--red); font-weight: 700; font-size: 30px; text-transform: uppercase;
  }
  .person-title { color: var(--grey-light); font-size: 24px; margin-top: 6px; }
  .person-rule { width: 220px; height: 1px; background: var(--rule); margin: 18px auto; }
  .person-contact { color: var(--grey-light); font-size: 24px; line-height: 1.4; }

  /* Back: company card */
  .pattern-field {
    position: absolute; left: 0; top: 0; width: 100%; height: 460px;
    background: linear-gradient(180deg, var(--pattern-top), var(--pattern-bottom));
  }
  .company-mark {
    position: absolute; right: 70px; top: 250px;
    display: flex; align-items: center; gap: 10px;
  }
  .company-mark .brand-square { width: 14px; height: 14px; margin-top: 0; }
  .company-mark .brand-name { font-size: 22px; }
  .company {
    position: absolute; left: 0; right: 0; top: 470px; text-align: center;
  }
  .company-name {
    color: var(--red); font-weight: 700; font-size: 28px; line-height: 1.15; text-transform: uppercase;
  }
  .company-phone { color: var(--grey-light); font-weight: 700; font-size: 34px; margin-top: 14px; }
  .company-web { color: var(--grey-light); font-size: 19px; margin-top: 18px; }
  .company-web .accent { color: var(--red); }
</style>
</head>
<body>
<main class="canvas">
  <section class="card card--person">
    <div class="brand-mark">
      <span class="brand-square"></span>
      <span class="brand-name">Tandem<br>Hearth<br>Works</span>
    </div>
    <div class="person">
      <h1 class="person-name">Marcus Ellery</h1>
      <p class="person-title">Managing Director</p>
      <div class="person-rule"></div>
      <p class="person-contact">555.0142.0142<br>name@tandemhearth.com</p>
    </div>
  </section>

  <section class="card card--company">
    <div class="pattern-field" role="img" aria-label="Faint repeated brand name pattern in dark grey"></div>
    <div class="company-mark">
      <span class="brand-square"></span>
      <span class="brand-name">Tandem Hearth Works</span>
    </div>
    <div class="company">
      <h2 class="company-name">Tandem Hearth<br>Works Pty Ltd</h2>
      <p class="company-phone">555.0190.0190</p>
      <p class="company-web">info@tandemhearth.com | www.<span class="accent">tandemhearth</span>.com</p>
    </div>
  </section>
</main>
</body>
</html>
```